Hybrid Seed corn and Soybean Sales business needs a website.

We here at "KW Grain" feel that we need a website to show a very professional side to our customer base. Although no actual ordering will take place on this website, we would like to put Plot and field trail data on the website. Along with a brief page for each of our hybrids and a place for customers to sign up for a newsletter. The company we sell hybrids for is MolvanGrain.com... Im not sure how this process works as far as myself updating the information or having the data actually put on the website, but feel free to contact me if you need the information. I will attach the logo for the company, (KW Grain).

Target Market(s)

Farmers, "Producers", Corn and soybean production

Industry/Entity Type

Business

Coding

Coded - Design and coding required

Number of Pages Required

5+ page

Colors
f78f20
ffffff

Requirements
Nice to have
• Similar layout to http://www.molvangrain.com/
• And it would be nice to incorporate our story into the website
• http://www.molvangrain.com/our-story/molvan-today/

```html
<!DOCTYPE html>
<html lang="en">
<head>
<meta charset="utf-8">
<title>KW Grain – Hybrid Seeds of Corn &amp; Soybean</title>
<link href="https://fonts.googleapis.com/css2?family=Roboto:ital,wght@0,400;0,500;0,700;1,400&family=Oswald:wght@400;500&family=Open+Sans:wght@400;600&display=swap" rel="stylesheet">
<style>
:root{
  --orange:#e8850c;
  --orange-light:#f78f20;
  --green:#4e9a12;
  --green-light:#7cc42a;
  --nav-dark:#2e2e2e;
  --text:#444;
  --heading-green:#3d8f12;
  --footer-bg:#f1f1f1;
  --bar:#1f1f1f;
  --white:#fff;
}
*{margin:0;padding:0;box-sizing:border-box}
html,body{width:802px;height:1200px;overflow:hidden;background:var(--white)}
body{position:relative;font-family:'Roboto',sans-serif;color:var(--text)}
.abs{position:absolute}

/* header */
.brand{left:60px;top:38px;display:flex;align-items:center;gap:8px;font:700 22px 'Roboto',sans-serif;color:var(--orange)}
.brand-dot{width:14px;height:14px;border-radius:50%;background:var(--green)}
.search{left:472px;top:36px;width:137px;height:24px;display:flex}
.search-field{flex:1;border:1px solid #9a9a9a;font:8px 'Roboto',sans-serif;color:#666;padding:0 6px;display:flex;align-items:center}
.search-btn{width:21px;background:var(--green);display:flex;align-items:center;justify-content:center}
.phone{left:628px;top:39px;display:flex;align-items:center;gap:6px;font:500 14px 'Roboto',sans-serif;color:#222}

/* nav */
.nav{left:0;top:91px;width:802px;height:40px;background:linear-gradient(#86c935,#4f9a10);box-shadow:0 3px 5px rgba(0,0,0,.35)}
.nav a{position:absolute;top:0;height:40px;display:flex;align-items:center;font:400 11px 'Roboto',sans-serif;color:var(--white);text-decoration:none;letter-spacing:.2px}
.nav a.active{background:var(--nav-dark);padding:0 22px;left:59px}

/* hero */
.hero{left:0;top:131px;width:802px;height:398px;background:linear-gradient(100deg,#b9c5a6 0%,#e0b03a 22%,#f2c12a 33%,#7e8e52 50%,#5b7232 70%,#8ea6c4 100%)}
.hero-title{right:60px;top:308px;text-align:right;font:500 29px/1 'Oswald',sans-serif;color:var(--white);text-shadow:0 1px 3px rgba(0,0,0,.5);letter-spacing:-.3px}
.hero-sub{right:60px;top:348px;text-align:right;font:400 21px/29px 'Oswald',sans-serif;color:var(--white);text-shadow:0 1px 3px rgba(0,0,0,.5);letter-spacing:-.3px}
.hero-arrows{left:687px;top:412px;display:flex;gap:1px}
.hero-arrows span{width:24px;height:30px;background:rgba(20,20,20,.8);display:flex;align-items:center;justify-content:center}

/* product cards */
.card{top:562px;width:163px;height:190px;background:var(--orange);text-align:center;color:var(--white);box-shadow:0 14px 10px -10px rgba(0,0,0,.25)}
.card-photo{width:92px;height:92px;border-radius:50%;border:3px solid var(--white);margin:9px auto 0}
.card h3{font:500 11.5px 'Roboto',sans-serif;margin-top:13px;letter-spacing:.2px}
.card p{font:7.3px/12px 'Open Sans',sans-serif;margin-top:5px}
.card .more{font:italic 7.5px 'Roboto',sans-serif;margin-top:9px;display:block}

/* about */
.about-title{left:58px;top:787px;font:400 14px 'Roboto',sans-serif;color:var(--heading-green)}
.about-text{left:60px;top:813px;width:351px;font:9.1px/17.6px 'Roboto',sans-serif;text-align:justify;color:#555}
.btn{background:linear-gradient(#f39a2c,#d87806);color:var(--white);font:500 8.5px 'Roboto',sans-serif;display:flex;align-items:center;justify-content:center;border-radius:2px;box-shadow:0 1px 2px rgba(0,0,0,.3)}
.read-more{left:59px;top:948px;width:79px;height:23px}

.video-frame{left:428px;top:785px;width:315px;height:192px;border:1px solid #bbb;box-shadow:0 0 3px rgba(0,0,0,.15)}
.video{left:436px;top:792px;width:299px;height:177px;border-radius:3px;overflow:hidden;background:#111}
.video-scene{width:299px;height:154px;background:radial-gradient(ellipse at 52% 95%,#ffd54a 0%,#f08a14 18%,#7a3a10 48%,#2c1a12 80%)}
.video-bar{height:23px;background:#161616;display:flex;align-items:center;padding:0 8px;gap:8px;font:7px 'Roboto',sans-serif;color:#ddd}

/* footer */
.footer{left:0;top:994px;width:802px;height:144px;background:linear-gradient(#fafafa,#e9e9e9);border-top:1px solid #ddd}
.partner{font:500 12px 'Roboto',sans-serif;color:#333}
.fhead{font:400 9.5px 'Roboto',sans-serif;color:var(--orange)}
.tweet{left:265px;top:1060px;width:110px;font:6px/9.5px 'Open Sans',sans-serif;color:#555}
.tweet b{display:block;font:600 7.5px 'Open Sans',sans-serif;color:#333;margin-bottom:1px}
.tweet a{display:block;color:#3aa3d8;margin-top:6px;text-decoration:none}
.links{left:404px;top:1050px;list-style:none;font:7.5px/15.3px 'Roboto',sans-serif;color:#555}
.links li::before{content:"";display:inline-block;border-left:4px solid #1f5d86;border-top:3.5px solid transparent;border-bottom:3.5px solid transparent;margin-right:7px}
.social{left:498px;top:1050px;font:7.5px 'Roboto',sans-serif;color:#555}
.social div{display:flex;align-items:center;gap:9px;height:20px}
.social i{width:16px;height:16px;border-radius:50%;border:2px solid #ccc;display:block}
.news-input{left:612px;top:1052px;width:131px;height:25px;border:1px solid #999;background:var(--white);font:italic 8px 'Roboto',sans-serif;color:#555;padding-left:7px;display:flex;align-items:center}
.signup{left:612px;top:1085px;width:59px;height:22px}
.bottom{left:0;top:1138px;width:802px;height:62px;background:var(--bar);color:#eee;font:9.5px 'Roboto',sans-serif;display:flex;align-items:center;justify-content:center}
</style>
</head>
<body>

<header>
  <div class="abs brand"><span class="brand-dot"></span>KW GRAIN</div>
  <div class="abs search">
    <div class="search-field">Search</div>
    <div class="search-btn"><svg width="9" height="9" viewBox="0 0 10 10"><circle cx="4" cy="4" r="3" fill="none" stroke="#fff" stroke-width="1.5"/><line x1="6.2" y1="6.2" x2="9" y2="9" stroke="#fff" stroke-width="1.6"/></svg></div>
  </div>
  <div class="abs phone">
    <svg width="12" height="12" viewBox="0 0 12 12"><rect width="12" height="12" rx="2" fill="#e8850c"/><path d="M3.5 2.8l1.3 1.5-.7 1a5 5 0 002.6 2.6l1-.7 1.5 1.3-.9 1.1C5.6 9.3 2.7 6.4 2.4 3.7z" fill="#fff"/></svg>
    1-800-555-0142
  </div>
</header>

<nav class="abs nav">
  <a class="active" href="#">HOME</a>
  <a style="left:156px" href="#">OUR STORY</a>
  <a style="left:259px" href="#">FRIENDS</a>
  <a style="left:349px" href="#">PRODUCTS</a>
  <a style="left:450px" href="#">EVENTS &amp; GETAWAYS</a>
  <a style="left:603px" href="#">BLOG</a>
  <a style="left:677px" href="#">CONTACT</a>
</nav>

<section class="abs hero" role="img" aria-label="Close-up of a ripe ear of yellow corn in a green corn field under blue sky"></section>
<h1 class="abs hero-title">WE SELL HYBRID SEEDS OF CORN</h1>
<p class="abs hero-sub">LOREM IPSUM IS SIMPLY DUMMY TEXT OF THE<br>PRINTING AND TYPESETTING INDUSTRY</p>
<div class="abs hero-arrows">
  <span><svg width="8" height="14" viewBox="0 0 8 14"><path d="M7 1L1 7l6 6" stroke="#fff" fill="none"/></svg></span>
  <span><svg width="8" height="14" viewBox="0 0 8 14"><path d="M1 1l6 6-6 6" stroke="#fff" fill="none"/></svg></span>
</div>

<section>
  <div class="abs card" style="left:58px">
    <div class="card-photo" role="img" aria-label="Corn kernels under a magnifying glass" style="background:radial-gradient(circle,#e9b560,#b8702a)"></div>
    <h3>HYBRID SEEDS OF CORN</h3>
    <p>Lorem Ipsum is simply dummy text<br>of the printing and type</p>
    <span class="more">Read More &gt;&gt;</span>
  </div>
  <div class="abs card" style="left:232px">
    <div class="card-photo" role="img" aria-label="Pile of soybeans" style="background:radial-gradient(circle,#f0cf7a,#c7963c)"></div>
    <h3>SOYBEAN</h3>
    <p>Lorem Ipsum is simply dummy text<br>of the printing and type</p>
    <span class="more">Read More &gt;&gt;</span>
  </div>
  <div class="abs card" style="left:407px">
    <div class="card-photo" role="img" aria-label="Yellow corn kernels" style="background:radial-gradient(circle,#fde0a6,#f2a650)"></div>
    <h3>HYBRID SEEDS OF CORN</h3>
    <p>Lorem Ipsum is simply dummy text<br>of the printing and type</p>
    <span class="more">Read More &gt;&gt;</span>
  </div>
  <div class="abs card" style="left:581px">
    <div class="card-photo" role="img" aria-label="Assorted beans: purple, green and beige" style="background:linear-gradient(#4a2a4e,#6b7a3a 50%,#e1c992)"></div>
    <h3>SOYBEAN</h3>
    <p>Lorem Ipsum is simply dummy text<br>of the printing and type</p>
    <span class="more">Read More &gt;&gt;</span>
  </div>
</section>

<section>
  <h2 class="abs about-title">ABOUT THE KW GRAIN</h2>
  <p class="abs about-text">Lorem Ipsum has been the industry's standard dummy text ever since the 1500s, when an unknown printer took a galley of type and scrambled it to make a type specimen book. It has survived not only five centuries, but also the leap into electronic typesetting, remaining essentially unchanged. It was popularised in the 1960s with the release of Letterset sheets containing Lorem Ipsum passages, and more recently with desktop publishing software like Pagemill Writer including versions of Lorem Ipsum</p>
  <div class="abs btn read-more">READ MORE</div>

  <div class="abs video-frame"></div>
  <div class="abs video">
    <div class="video-scene" role="img" aria-label="Video still: sunset over a field"></div>
    <div class="video-bar">
      <svg width="11" height="11" viewBox="0 0 12 12"><circle cx="6" cy="6" r="5" fill="none" stroke="#ddd" stroke-width="1.3"/><path d="M5 3.8v4.4L8.3 6z" fill="#ddd"/></svg>
      <svg width="9" height="8" viewBox="0 0 9 8"><path d="M0 2.5h2l3-2.5v8L2 5.5H0z" fill="#e23b3b"/></svg>
      <svg width="115" height="6" viewBox="0 0 115 6"><rect x="0" y="1" width="20" height="4" fill="#e23b3b"/><rect x="30" y="2" width="85" height="2" fill="#555"/><rect x="30" y="2" width="45" height="2" fill="#e23b3b"/></svg>
      <span style="margin-left:auto">01:30 / 04:55</span>
      <svg width="9" height="7" viewBox="0 0 9 7"><rect x=".5" y=".5" width="8" height="6" fill="none" stroke="#ddd"/></svg>
      <svg width="8" height="8" viewBox="0 0 8 8"><circle cx="4" cy="4" r="3" fill="none" stroke="#ddd" stroke-width="1.6" stroke-dasharray="1.5 1"/></svg>
    </div>
  </div>
  <svg class="abs" style="left:567px;top:846px" width="34" height="34" viewBox="0 0 34 34"><circle cx="17" cy="17" r="16" fill="rgba(0,0,0,.55)" stroke="#bbb"/><path d="M13 10v14l11-7z" fill="#fff"/></svg>
</section>

<footer>
  <div class="abs footer"></div>
  <div class="abs partner" style="left:61px;top:1028px">Fieldway</div>
  <div class="abs partner" style="left:61px;top:1065px">Norrow Crop Partners</div>
  <div class="abs partner" style="left:61px;top:1102px">Molvan</div>

  <div class="abs fhead" style="left:234px;top:1023px">CHIRPER</div>
  <svg class="abs" style="left:234px;top:1058px" width="20" height="20" viewBox="0 0 20 20"><circle cx="10" cy="10" r="8" fill="#3aa3d8"/></svg>
  <div class="abs tweet"><b>FieldNote Tweets 1</b>Online and high-tech start-ups could account for 4% of Australia's GDP and 540,000 jobs by 2033<a href="#">http://fieldnote.example/7k2a</a></div>

  <div class="abs fhead" style="left:403px;top:1023px">LINKS</div>
  <ul class="abs links"><li>Home</li><li>Our Team</li><li>Listings</li><li>Services</li></ul>

  <div class="abs fhead" style="left:497px;top:1023px">CONNECT US</div>
  <div class="abs social">
    <div><i style="background:#2f5c9a"></i>Facepage</div>
    <div><i style="background:#2a8fd6"></i>Chirper</div>
    <div style="margin-top:1px"><i style="background:#d63b2e"></i>Globe+</div>
  </div>

  <div class="abs fhead" style="left:612px;top:1023px">NEWSLETTER</div>
  <div class="abs news-input">Enter Your Mail Id</div>
  <div class="abs btn signup">SIGN UP</div>

  <div class="abs bottom">Copyright © 2015 &nbsp;All Rights Reserved</div>
</footer>

</body>
</html>
```